Company identity deisgn should support 2 languages

I would like to get our company identity design
This includes the following only
Business Cards 2 languages Arabic and English
Email signature
Letterhead
Linkedin profile images
Attached is the logo in Ai format

Requirements
Must have
• For business card
Must have
Name and Adrees in arabic
Name and Address in english
You might use both side of the card
Should not have
• Any pictures other than the logo

```html
<!DOCTYPE html>
<html lang="en">
<head>
<meta charset="utf-8">
<title>Nexora Cognitive Systems – Identity</title>
<link href="https://fonts.googleapis.com/css2?family=Roboto:wght@400;500;700&family=Open+Sans:wght@400&family=Noto+Naskh+Arabic:wght@400;500&display=swap" rel="stylesheet">
<style>
:root{
  --blue:#1d74c0;
  --blue-light:#2a9ad8;
  --grey:#6d6e71;
  --text:#4a4a4a;
  --stage-dark:#2c2c2c;
  --stage-light:#dedfe0;
  --paper:#ffffff;
  --paper-tint:#f6f7f9;
  --faint:#e4eaf5;
}
*{margin:0;padding:0;box-sizing:border-box}
html,body{width:1200px;height:2164px;overflow:hidden}
body{position:relative;background:var(--stage-light);font-family:"Roboto",Arial,sans-serif;color:var(--text)}
.arabic{font-family:"Noto Naskh Arabic",serif}
.stage-top{position:absolute;left:0;top:0;width:1200px;height:867px;background:var(--stage-dark)}

/* business cards */
.card{position:absolute;width:520px;height:300px;box-shadow:0 12px 30px rgba(0,0,0,.45);overflow:hidden}
.card-front{left:50px;top:283px;background:linear-gradient(135deg,var(--blue),var(--blue-light))}
.card-back{left:630px;top:283px;background:var(--paper)}
.brand{display:flex;align-items:center;gap:10px;font-weight:500;letter-spacing:.06em;white-space:nowrap}
.brand-dot{border-radius:50%;flex:none}
.card-front .brand{position:absolute;left:70px;top:128px;color:#fff;font-size:24px}
.card-front .brand-dot{width:34px;height:34px;background:#fff}
.card-front .brand-ar{position:absolute;left:116px;top:166px;color:#fff;font-size:16px;opacity:.9}

.card-back .brand{position:absolute;right:28px;top:26px;color:var(--blue);font-size:14px}
.card-back .brand-dot{width:22px;height:22px;background:var(--blue)}
.card-back .brand-ar{position:absolute;right:28px;top:50px;color:var(--grey);font-size:11px}
.card-name{position:absolute;left:28px;top:96px;color:var(--blue);font-weight:700;font-size:19px;white-space:nowrap}
.card-name .arabic{font-weight:500}
.card-role{position:absolute;left:28px;top:122px;font-size:13px;font-weight:500}
.card-addr-ar{position:absolute;left:28px;top:148px;font-size:12px;line-height:1.45}
.card-contact{position:absolute;left:28px;top:200px;font-size:12px;line-height:1.5;list-style:none}
.card-contact li{display:flex;align-items:center;gap:6px}
.card-addr-en{position:absolute;right:28px;top:218px;font-size:12px;text-align:right;line-height:1.45}
.ico{width:12px;height:12px;fill:var(--blue);flex:none}

.band{position:absolute;left:0;bottom:0;width:100%;height:10px;display:flex}
.band-blue{flex:0 0 64%;background:var(--blue);clip-path:polygon(0 0,100% 0,98.5% 100%,0 100%)}
.band-grey{flex:1;background:var(--grey);margin-left:-4px}

/* letterheads */
.letterhead{position:absolute;top:980px;width:418px;height:584px;background:linear-gradient(180deg,var(--paper),var(--paper-tint));box-shadow:0 6px 18px rgba(0,0,0,.18);overflow:hidden}
.lh-left{left:158px}
.lh-right{left:614px}
.letterhead .brand{position:absolute;left:36px;top:64px;color:var(--blue);font-size:8px;gap:5px}
.letterhead .brand-dot{width:14px;height:14px;background:var(--blue)}
.lh-contact{position:absolute;left:268px;top:42px;font-size:8px;line-height:1.45;list-style:none}
.lh-contact li{display:flex;align-items:center;gap:3px}
.lh-contact .ico{width:7px;height:7px}
.lh-body{position:absolute;left:37px;top:152px;width:346px;font-family:"Open Sans",Arial,sans-serif;font-size:6.6px;line-height:1.68;text-align:justify;color:#555}
.lh-body p{margin-bottom:8.5px}
.lh-body .greet{margin-bottom:11px}
.lh-body .close{margin-top:22px}
.signature{position:absolute;left:38px;top:420px;width:50px;height:42px;background:linear-gradient(135deg,#d9d9d9,#bfbfbf);opacity:.6;border-radius:4px}
.lh-mark{position:absolute;right:-10px;bottom:20px;width:120px;height:120px;border-radius:50%;background:var(--faint)}
.letterhead .band{height:8px}

/* email signature */
.email-sig{position:absolute;left:162px;top:1721px;width:880px;height:296px;background:var(--paper);box-shadow:0 6px 16px rgba(0,0,0,.22);overflow:hidden}
.sig-mark{position:absolute;right:40px;top:-20px;width:260px;height:260px;border-radius:50%;background:var(--faint)}
.sig-name{position:absolute;left:57px;top:46px;color:var(--blue);font-weight:700;font-size:27px;white-space:nowrap}
.sig-name .arabic{font-weight:500}
.sig-role{position:absolute;left:57px;top:82px;font-size:20px;font-weight:500}
.sig-addr-ar{position:absolute;left:57px;top:118px;font-size:19px;line-height:1.5}
.sig-contact{position:absolute;left:57px;top:182px;font-size:20px;line-height:1.35;list-style:none}
.sig-contact li{display:flex;align-items:center;gap:6px}
.sig-contact .ico{width:18px;height:18px}
.sig-addr-en{position:absolute;right:57px;top:212px;font-size:20px;text-align:right;line-height:1.35}
</style>
</head>
<body>
<svg width="0" height="0" style="position:absolute">
  <defs>
    <symbol id="i-phone" viewBox="0 0 24 24"><path d="M3 9c0-3 4-5 9-5s9 2 9 5l-3 1-2-2H8L6 10zM6 11h12l2 8H4z"/></symbol>
    <symbol id="i-mail" viewBox="0 0 24 24"><path d="M2 5h20v14H2zM3.5 6.5 12 13l8.5-6.5v-.1H3.5z" fill-rule="evenodd"/></symbol>
    <symbol id="i-globe" viewBox="0 0 24 24"><circle cx="12" cy="12" r="10"/><path d="M7 6c3 1 4 3 2 5s-1 4 1 6M15 4c-1 3 2 4 4 5" stroke="#fff" stroke-width="1.6" fill="none"/></symbol>
  </defs>
</svg>

<section class="stage-top">
  <article class="card card-front">
    <div class="brand"><span class="brand-dot"></span>NEXORA COGNITIVE SYSTEMS</div>
    <div class="brand-ar arabic" dir="rtl">شركة نكسورا للأنظمة</div>
  </article>

  <article class="card card-back">
    <div class="brand"><span class="brand-dot"></span>NEXORA COGNITIVE SYSTEMS</div>
    <div class="brand-ar arabic" dir="rtl">شركة نكسورا للأنظمة</div>
    <div class="card-name">KARIM VELLANO <span class="arabic">(كريم فيلانو)</span></div>
    <div class="card-role">Managing Director</div>
    <div class="card-addr-ar arabic" dir="rtl" style="text-align:left">٤٢ طريق هاربر بند، ليكفيو<br>بي سي كندا V2X 4K7</div>
    <ul class="card-contact">
      <li><svg class="ico"><use href="#i-phone"/></svg>555.210.4870</li>
      <li><svg class="ico"><use href="#i-mail"/></svg>info@nexoramail.com</li>
      <li><svg class="ico"><use href="#i-globe"/></svg>www.nexoraweb.com</li>
    </ul>
    <div class="card-addr-en">42 Harbor Bend Rd, Lakeview<br>B.C. Canada V2X 4K7</div>
    <div class="band"><span class="band-blue"></span><span class="band-grey"></span></div>
  </article>
</section>

<article class="letterhead lh-left">
  <div class="brand"><span class="brand-dot"></span>NEXORA COGNITIVE SYSTEMS</div>
  <ul class="lh-contact">
    <li>42 Harbor Bend Rd, Lakeview</li>
    <li>B.C. Canada V2X 4K7</li>
    <li><svg class="ico"><use href="#i-phone"/></svg>555.210.4870</li>
    <li><svg class="ico"><use href="#i-mail"/></svg>info@nexoramail.com</li>
    <li><svg class="ico"><use href="#i-globe"/></svg>www.nexoraweb.com</li>
  </ul>
  <div class="lh-body">
    <p class="greet">Dear customer,</p>
    <p>Lorem ipsum dolor sit amet, consectetur adipisicing elit, sed do eiusmod tempor incididunt ut labore et dolore magna aliqua. Ut enim ad minim veniam, quis nostrud exercitation ullamco laboris nisi ut aliquip ex ea commodo consequat. Duis aute irure dolor in reprehenderit in voluptate velit esse cillum dolore eu fugiat nulla pariatur. Excepteur sint occaecat cupidatat non proident, sunt in culpa qui officia deserunt mollit anim id est laborum.</p>
    <p>Lorem ipsum dolor sit amet, consectetur adipisicing elit, sed do eiusmod tempor incididunt ut labore et dolore magna aliqua. Ut enim ad minim veniam, quis nostrud exercitation ullamco laboris nisi ut aliquip ex ea commodo consequat. Duis aute irure dolor in reprehenderit in voluptate velit esse cillum dolore eu fugiat nulla pariatur. Excepteur sint occaecat cupidatat non proident, sunt in culpa qui officia deserunt mollit anim id est laborum.</p>
    <p>Lorem ipsum dolor sit amet, consectetur adipisicing elit, sed do eiusmod tempor incididunt ut labore et dolore magna aliqua. Ut enim ad minim veniam, quis nostrud exercitation ullamco laboris nisi ut aliquip ex ea commodo consequat. Duis aute irure dolor in reprehenderit in voluptate velit esse cillum dolore eu fugiat nulla pariatur. Excepteur sint occaecat cupidatat non proident, sunt in culpa qui officia deserunt mollit anim id est laborum.</p>
    <p class="close">Yours Sincerely,</p>
  </div>
  <div class="signature" role="img" aria-label="Handwritten signature"></div>
  <div class="lh-mark"></div>
  <div class="band"><span class="band-blue"></span><span class="band-grey"></span></div>
</article>

<article class="letterhead lh-right">
  <div class="brand"><span class="brand-dot"></span>NEXORA COGNITIVE SYSTEMS</div>
  <ul class="lh-contact">
    <li>42 Harbor Bend Rd, Lakeview</li>
    <li>B.C. Canada V2X 4K7</li>
    <li><svg class="ico"><use href="#i-phone"/></svg>555.210.4870</li>
    <li><svg class="ico"><use href="#i-mail"/></svg>info@nexoramail.com</li>
    <li><svg class="ico"><use href="#i-globe"/></svg>www.nexoraweb.com</li>
  </ul>
  <div class="lh-body">
    <p class="greet">Dear customer,</p>
    <p>Lorem ipsum dolor sit amet, consectetur adipisicing elit, sed do eiusmod tempor incididunt ut labore et dolore magna aliqua. Ut enim ad minim veniam, quis nostrud exercitation ullamco laboris nisi ut aliquip ex ea commodo consequat. Duis aute irure dolor in reprehenderit in voluptate velit esse cillum dolore eu fugiat nulla pariatur. Excepteur sint occaecat cupidatat non proident, sunt in culpa qui officia deserunt mollit anim id est laborum.</p>
    <p>Lorem ipsum dolor sit amet, consectetur adipisicing elit, sed do eiusmod tempor incididunt ut labore et dolore magna aliqua. Ut enim ad minim veniam, quis nostrud exercitation ullamco laboris nisi ut aliquip ex ea commodo consequat. Duis aute irure dolor in reprehenderit in voluptate velit esse cillum dolore eu fugiat nulla pariatur. Excepteur sint occaecat cupidatat non proident, sunt in culpa qui officia deserunt mollit anim id est laborum.</p>
    <p>Lorem ipsum dolor sit amet, consectetur adipisicing elit, sed do eiusmod tempor incididunt ut labore et dolore magna aliqua. Ut enim ad minim veniam, quis nostrud exercitation ullamco laboris nisi ut aliquip ex ea commodo consequat. Duis aute irure dolor in reprehenderit in voluptate velit esse cillum dolore eu fugiat nulla pariatur. Excepteur sint occaecat cupidatat non proident, sunt in culpa qui officia deserunt mollit anim id est laborum.</p>
    <p class="close">Yours Sincerely,</p>
  </div>
  <div class="signature" role="img" aria-label="Handwritten signature"></div>
  <div class="lh-mark"></div>
  <div class="band"><span class="band-blue"></span><span class="band-grey"></span></div>
</article>

<article class="email-sig">
  <div class="sig-mark"></div>
  <div class="sig-name">KARIM VELLANO <span class="arabic">(كريم فيلانو)</span></div>
  <div class="sig-role">Managing Director</div>
  <div class="sig-addr-ar arabic" dir="rtl" style="text-align:left">٤٢ طريق هاربر بند، ليكفيو<br>بي سي كندا V2X 4K7</div>
  <ul class="sig-contact">
    <li><svg class="ico"><use href="#i-phone"/></svg>555.210.4870</li>
    <li><svg class="ico"><use href="#i-mail"/></svg>info@nexoramail.com</li>
    <li><svg class="ico"><use href="#i-globe"/></svg>www.nexoraweb.com</li>
  </ul>
  <div class="sig-addr-en">42 Harbor Bend Rd, Lakeview<br>B.C. Canada V2X 4K7</div>
</article>
</body>
</html>
```